Its time for a new website

We are at a point now where we are in desperate need of a new website. It was last updated 2006 but still looks like its 1995. We are looking for something eye catching to our clients but easy to navigate and add/remove photos of jobs/trucks and information. Our key business is the manufacture of fire appliances and resale of parts and equipment.

www.kestrelrigs.com.au

Coding

Coded - Design and coding required

Number of Pages Required

5+ page

Requirements
Must have
• Logo

```html
<!DOCTYPE html>
<html lang="en">
<head>
<meta charset="utf-8">
<title>Kestrel Rigs — Fire Appliances</title>
<link href="https://fonts.googleapis.com/css2?family=Crimson+Text:wght@400;600&family=Open+Sans:wght@400;600;700&display=swap" rel="stylesheet">
<style>
:root{
  --red:#e4121b;
  --red-soft:#f26a6f;
  --blue:#0c7ac3;
  --blue-soft:#4ea4dc;
  --ink:#333333;
  --muted:#777777;
  --grey-band:#efefef;
  --dark:#231f20;
  --charcoal:#3a3a3a;
  --tab-grey:#555555;
  --white:#ffffff;
}
*{box-sizing:border-box;margin:0;padding:0}
html,body{width:1200px;height:2242px;overflow:hidden;background:var(--white)}
body{position:relative;font-family:"Open Sans",Arial,sans-serif;color:var(--ink)}
.abs{position:absolute}

/* header */
.site-header{left:0;top:0;width:1200px;height:145px;background:#fbfaf8}
.brand{left:82px;top:22px;width:170px;height:100px;display:flex;flex-direction:column;align-items:center}
.brand-mark{width:56px;height:56px;border-radius:50%;background:var(--blue);margin-bottom:8px}
.brand-name{font-size:21px;font-weight:600;color:var(--blue);white-space:nowrap}
.main-nav a{position:absolute;top:93px;font-size:13px;color:var(--ink);text-decoration:none;white-space:nowrap}
.main-nav a.active{color:var(--blue)}
.nav-indicator{left:353px;top:139px;width:67px;height:6px;background:var(--blue)}

/* hero */
.hero{left:0;top:145px;width:1200px;height:381px;background:linear-gradient(180deg,#8e9a93 0%,#b53a3a 45%,#8d2a2b 70%,#6b6a66 100%)}
.hero-caption{left:607px;top:495px;width:512px;height:52px;display:flex}
.hero-caption .arrow{width:47px;background:var(--blue-soft);display:flex;align-items:center;justify-content:center}
.hero-caption .text{flex:1;background:var(--blue);color:var(--white);font-size:20px;display:flex;align-items:center;padding-left:20px}

/* welcome */
.welcome-title{left:0;top:585px;width:1200px;text-align:center;font-family:"Crimson Text",Georgia,serif;font-size:28px;font-weight:400;color:var(--ink)}
.welcome-title .hl-red{color:var(--red)}
.welcome-title .hl-blue{color:var(--blue)}
.welcome-copy{left:120px;top:643px;width:960px;text-align:center;font-size:11.5px;line-height:26.5px;color:var(--muted)}
.btn{display:flex;height:100%;font-size:12px;font-weight:400;color:var(--white);text-decoration:none}
.btn .label{flex:1;display:flex;align-items:center;justify-content:center}
.btn .chev{width:32%;display:flex;align-items:center;justify-content:center}
.btn-red .label{background:var(--red)}.btn-red .chev{background:var(--red-soft)}
.btn-blue .label{background:var(--blue)}.btn-blue .chev{background:var(--blue-soft)}
.btn-dark .label{background:var(--charcoal)}.btn-dark .chev{background:#555}
.welcome-btn{left:523px;top:777px;width:154px;height:40px}

/* services */
.services{left:0;top:867px;width:1200px;height:478px;background:var(--grey-band)}
.section-title{left:0;width:1200px;text-align:center;font-family:"Crimson Text",Georgia,serif;font-size:26px;font-weight:400;color:var(--ink)}
.service{width:260px;text-align:center}
.service-icon{width:134px;height:134px;border-radius:50%;margin:0 auto;background:var(--white);border:6px solid #e6e6e6;display:flex;align-items:center;justify-content:center}
.service-icon.active{background:var(--blue);border-color:var(--white);box-shadow:0 0 0 2px var(--blue)}
.service h3{margin-top:28px;font-size:16px;font-weight:600;color:var(--ink)}
.service.active h3{color:var(--blue)}
.service p{margin-top:12px;font-size:11px;line-height:26.5px;color:var(--muted);padding:0 16px}
.service .btn{width:124px;height:39px;margin:24px auto 0;font-size:11px}

/* featured */
.tabs{left:399px;top:1449px;display:flex;gap:9px}
.tab{height:23px;width:94px;background:var(--tab-grey);color:var(--white);font-size:12px;display:flex;align-items:center;justify-content:center}
.tab.active{background:var(--red)}
.tabs-rule{left:0;top:1473px;width:1200px;height:1px;background:#dcdcdc}
.card{top:1509px;width:239px;height:326px;border:1px solid #e0e0e0;background:var(--white);text-align:center;padding:5px}
.card-photo{height:168px;width:100%}
.card h4{margin-top:16px;font-size:11.5px;font-weight:700;color:var(--ink)}
.card p{margin-top:6px;font-size:11px;line-height:21px;color:var(--muted)}
.card .more{display:inline-block;margin-top:6px;background:var(--blue);color:var(--white);font-size:11px;padding:3px 8px}
.carousel-arrow{top:1660px}

/* footer */
.site-footer{left:0;top:1889px;width:1200px;height:303px;background:var(--dark)}
.footer-col{top:1932px;color:var(--white)}
.footer-col h5{font-size:12px;font-weight:700;letter-spacing:.5px;margin-bottom:22px;color:var(--white)}
.footer-col p{font-size:12px;line-height:26px;color:#e6e6e6}
.footer-col .link{color:var(--blue);text-decoration:underline;font-size:12px}
.quick-links{display:flex;flex-wrap:wrap;gap:9px 7px;width:212px}
.quick-links span{border:1px solid #8a8a8a;font-size:11px;color:#e6e6e6;height:38px;padding:0 7px;display:flex;align-items:center}
.info-line{font-size:12px;line-height:27px;color:#e6e6e6;white-space:nowrap}
.info-line b{color:var(--blue);font-weight:400}
.social{display:flex;gap:16px}
.social span{width:33px;height:33px;border-radius:4px}
.copyright{left:0;top:2192px;width:1200px;height:50px;background:var(--red);color:var(--white);font-size:11px;display:flex;align-items:center;justify-content:center;letter-spacing:.3px}
</style>
</head>
<body>

<header class="abs site-header">
  <div class="abs brand">
    <span class="brand-mark"></span>
    <span class="brand-name">Kestrel Rigs</span>
  </div>
  <nav class="main-nav">
    <a class="active" style="left:367px">Home</a>
    <a style="left:437px">About Us</a>
    <a style="left:523px">Pumpers</a>
    <a style="left:611px">Tankers</a>
    <a style="left:690px">GPA/Rescue</a>
    <a style="left:792px">Light Tankers</a>
    <a style="left:895px">Trailers</a>
    <a style="left:971px">Slip-on-Units</a>
    <a style="left:1073px">Contact</a>
  </nav>
  <div class="abs nav-indicator"></div>
</header>

<div class="abs hero" role="img" aria-label="Photo of a red fire engine with firefighters in turnout gear working at its pump panel"></div>
<div class="abs hero-caption">
  <span class="arrow"><svg width="14" height="20" viewBox="0 0 14 20"><path d="M11 2 3 10l8 8" fill="none" stroke="#fff" stroke-width="2.5"/></svg></span>
  <span class="text">Western Australia's leading manufacturer</span>
  <span class="arrow"><svg width="14" height="20" viewBox="0 0 14 20"><path d="M3 2l8 8-8 8" fill="none" stroke="#fff" stroke-width="2.5"/></svg></span>
</div>

<h1 class="abs welcome-title">Welcome to Our <span class="hl-red">Fire</span> <span class="hl-blue">Applications</span> !</h1>
<p class="abs welcome-copy">Kestrel Rigs are Western Australia's Largest, most experienced and competent manufacturer of today's fire fighting vehicles.<br>Fire-Brigade Captain and 35-year veteran volunteer Fire-fighter, Daniel Harlow, established Kestrel Rigs in 1988. As a fully Qualified automotive motor mechanic, he has<br>gained the necessary experience and expertise required to develop an ever increasing range of high Quality, Functional and Affordable fire<br>appliances suited to the harsh Australian environment.</p>
<div class="abs welcome-btn"><a class="btn btn-red"><span class="label">READ MORE</span><span class="chev">»</span></a></div>

<section class="abs services"></section>
<h2 class="abs section-title" style="top:897px">Our Services</h2>

<div class="abs service active" style="left:79px;top:964px">
  <div class="service-icon active"><svg width="50" height="40" viewBox="0 0 50 40"><path d="M8 30l14-14 6 2 10-10 6 6-10 10 2 6-14 14z" fill="#fff"/></svg></div>
  <h3>PUMPERS</h3>
  <p>Our range of pumpers have been specifically designed for use in a broad range of areas such as metropolitan,</p>
  <a class="btn btn-dark"><span class="label">READ MORE</span><span class="chev">»</span></a>
</div>
<div class="abs service" style="left:338px;top:964px">
  <div class="service-icon"><svg width="76" height="36" viewBox="0 0 76 36"><rect x="2" y="8" width="16" height="18" fill="#444"/><rect x="20" y="4" width="52" height="22" rx="9" fill="#444"/><rect x="2" y="24" width="72" height="4" fill="#444"/><circle cx="12" cy="30" r="5" fill="#444"/><circle cx="52" cy="30" r="5" fill="#444"/><circle cx="64" cy="30" r="5" fill="#444"/></svg></div>
  <h3>TANKERS</h3>
  <p>Our range of pumpers have been specifically designed for use in a broad range of areas such as metropolitan,</p>
  <a class="btn btn-blue"><span class="label">READ MORE</span><span class="chev">»</span></a>
</div>
<div class="abs service" style="left:596px;top:964px">
  <div class="service-icon"><svg width="72" height="38" viewBox="0 0 72 38"><rect x="2" y="4" width="48" height="24" fill="#444"/><path d="M52 12h10l8 8v8H52z" fill="#444"/><circle cx="14" cy="31" r="5" fill="#444"/><circle cx="40" cy="31" r="5" fill="#444"/><circle cx="62" cy="31" r="5" fill="#444"/></svg></div>
  <h3>TRAILERS</h3>
  <p>Our range of pumpers have been specifically designed for use in a broad range of areas such as metropolitan,</p>
  <a class="btn btn-blue"><span class="label">READ MORE</span><span class="chev">»</span></a>
</div>
<div class="abs service" style="left:858px;top:964px">
  <div class="service-icon"><svg width="44" height="44" viewBox="0 0 44 44"><rect x="8" y="8" width="28" height="28" rx="4" fill="#444"/><rect x="19" y="13" width="6" height="18" fill="#fff"/><rect x="13" y="19" width="18" height="6" fill="#fff"/></svg></div>
  <h3>GPA / RESCUE</h3>
  <p>Our range of pumpers have been specifically designed for use in a broad range of areas such as metropolitan,</p>
  <a class="btn btn-blue"><span class="label">READ MORE</span><span class="chev">»</span></a>
</div>

<h2 class="abs section-title" style="top:1388px">Featured Manufacturing Equipments</h2>
<div class="abs tabs">
  <span class="tab active">Pumpers</span><span class="tab">Trailers</span><span class="tab">Tankers</span><span class="tab">Rescue/ GPA</span>
</div>
<div class="abs tabs-rule"></div>

<svg class="abs carousel-arrow" style="left:30px" width="16" height="30" viewBox="0 0 16 30"><path d="M13 3 3 15l10 12" fill="none" stroke="#aaa" stroke-width="2"/></svg>
<svg class="abs carousel-arrow" style="left:1154px" width="16" height="30" viewBox="0 0 16 30"><path d="M3 3l10 12-10 12" fill="none" stroke="#aaa" stroke-width="2"/></svg>

<article class="abs card" style="left:82px">
  <div class="card-photo" role="img" aria-label="Photo of a tanker truck under a blue hover overlay" style="background:linear-gradient(180deg,#2b86d0,#1565b0)"></div>
  <h4>LOREM IPSUM SIMPLY DUMMY</h4>
  <p>cab chassis with a Altmark KT440<br>Manual Turret capable of<br>delivering water........&gt;&gt;</p>
  <span class="more">More Info</span>
</article>
<article class="abs card" style="left:347px">
  <div class="card-photo" role="img" aria-label="Photo of a red and white fire appliance cab" style="background:linear-gradient(180deg,#b9b4ab,#c4302e 55%,#5a4a44)"></div>
  <h4>LOREM IPSUM SIMPLY DUMMY</h4>
  <p>cab chassis with a Altmark KT440<br>Manual Turret capable of<br>delivering water........&gt;&gt;</p>
  <span class="more">More Info</span>
</article>
<article class="abs card" style="left:614px">
  <div class="card-photo" role="img" aria-label="Photo of a red fire truck with yellow striping parked outdoors" style="background:linear-gradient(180deg,#7a8a92,#b02a2a 55%,#8c7a62)"></div>
  <h4>LOREM IPSUM SIMPLY DUMMY</h4>
  <p>cab chassis with a Altmark KT440<br>Manual Turret capable of<br>delivering water........&gt;&gt;</p>
  <span class="more">More Info</span>
</article>
<article class="abs card" style="left:880px">
  <div class="card-photo" role="img" aria-label="Photo of a white light tanker truck outside a workshop" style="background:linear-gradient(180deg,#9aa3a6,#e4e4e2 55%,#a08a70)"></div>
  <h4>LOREM IPSUM SIMPLY DUMMY</h4>
  <p>cab chassis with a Altmark KT440<br>Manual Turret capable of<br>delivering water........&gt;&gt;</p>
  <span class="more">More Info</span>
</article>

<footer class="abs site-footer"></footer>
<div class="abs footer-col" style="left:82px;width:250px">
  <h5>FOR EMPLOYMENT OPPURTUNITIES</h5>
  <p>Lorem ipsum dolor sit amet, consectetur adipi sicing elit, sed do eiusmod tempor</p>
  <a class="link">CLICK HERE</a>
</div>
<div class="abs footer-col" style="left:392px">
  <h5>QUICK LINKS</h5>
  <div class="quick-links">
    <span>Pumpers</span><span>GPA / Rescue</span><span>Tankers</span><span>Trailers</span><span>New</span><span>Slip on Unit</span><span>Contact</span><span>About</span>
  </div>
</div>
<div class="abs footer-col" style="left:668px;width:200px">
  <h5>INFO</h5>
  <p style="line-height:26px;font-size:11.5px">You can contact or visit us during working time.</p>
  <div style="margin-top:14px">
    <div class="info-line"><b>Tel:</b>&nbsp; 08 9000 4417</div>
    <div class="info-line"><b>Email:</b> info@kestrelrigs.com.au</div>
    <div class="info-line"><b>Working Hours</b>: 8:00 a.m-17:00 a.m</div>
  </div>
</div>
<div class="abs footer-col" style="left:937px">
  <h5>FOLLOW US</h5>
  <div class="social" aria-label="Social links">
    <span style="background:#4a6fb5"></span><span style="background:#e8761c"></span><span style="background:#2f94d9"></span><span style="background:#e4121b"></span>
  </div>
</div>
<div class="abs copyright">© COPYRIGHT 2015. KESTREL RIGS. ALL RIGHTS RESERVED.</div>

</body>
</html>
```